Brightway Haul & Upkeep Services, are a company that offers a 'one stop shop' pre-move clean up a

I have already selected a logo which I would like on the front of the business cards along with phone numbers, web address and email which are:
0487650392
www.brightwayhaul.com.au
brightwayhaulandupkeep@mailbox.example

On the back of the card I would like to list some of the types of service we offer (clean - move - repairs/maintenance) which are:
CLEAN - windows, gutters, solar panels, driveways/paths, carpets.
MOVE - Small/medium size house/office moves, large item pick-up & delivery, yard clean-up and removal.
General maintenance and repairs.

I would like the blue logo on a gray background.

Thanks

```html
<!DOCTYPE html>
<html lang="en">
<head>
<meta charset="utf-8">
<title>Brightway Haul &amp; Upkeep Services – Business Card</title>
<link rel="stylesheet" href="https://fonts.googleapis.com/css2?family=Open+Sans:wght@400;600;700;800&display=swap">
<style>
  :root {
    --page: #e9eaec;
    --card: #ffffff;
    --brand-blue: #2d6db5;
    --panel-blue: #8fb3d9;
    --faint-blue: #d3e1f1;
    --ink: #1e1e1e;
    --on-panel: #ffffff;
  }
  * { box-sizing: border-box; margin: 0; padding: 0; }
  html, body {
    width: 1200px; height: 379px; overflow: hidden;
    background: var(--page);
    font-family: "Open Sans", Arial, sans-serif;
  }
  .sheet { position: relative; width: 1200px; height: 379px; }
  .card {
    position: absolute; top: 28px;
    width: 556px; height: 317px;
    background: var(--card);
    box-shadow: 0 2px 6px rgba(0,0,0,.18);
    overflow: hidden;
  }
  .card--front { left: 30px; }
  .card--back { left: 612px; }

  /* Front */
  .front-accent {
    position: absolute; left: 300px; top: 96px;
    width: 221px; height: 221px;
    background: var(--faint-blue);
  }
  .brand-name {
    position: absolute; left: 26px; top: 74px; z-index: 1;
    color: var(--brand-blue); font-weight: 800;
    text-transform: uppercase; line-height: 1.05;
  }
  .brand-name__main { display: block; font-size: 45px; letter-spacing: .5px; }
  .brand-name__sub { display: block; font-size: 21px; margin-top: 8px; letter-spacing: .4px; }

  .contact-phone {
    position: absolute; left: 24px; top: 258px; z-index: 1;
    display: flex; align-items: center; gap: 6px;
    font-size: 19px; color: var(--ink); letter-spacing: .3px;
  }
  .contact-phone svg { width: 16px; height: 16px; }
  .contact-web {
    position: absolute; right: 12px; top: 252px; z-index: 1;
    font-size: 15.5px; color: var(--ink); letter-spacing: .3px;
  }
  .contact-email {
    position: absolute; right: 12px; top: 277px; z-index: 1;
    display: flex; align-items: center; gap: 5px;
    font-size: 12px; color: var(--ink);
  }
  .contact-email svg { width: 11px; height: 9px; }

  /* Back */
  .back-accent {
    position: absolute; left: 370px; top: 60px;
    width: 80px; height: 80px;
    background: var(--panel-blue);
  }
  .services-panel {
    position: absolute; left: 24px; top: 132px;
    width: 506px; height: 114px;
    background: var(--panel-blue); border-radius: 14px;
    color: var(--on-panel); text-align: center;
  }
  .services-panel__title {
    margin-top: 14px; margin-left: -40px;
    font-size: 19px; font-weight: 600; letter-spacing: 1.6px;
  }
  .services-panel__list { list-style: none; margin-top: 13px; font-size: 16px; font-weight: 600; line-height: 1.3; }
  .services-panel__list li { margin-top: 4px; margin-left: -40px; }
  .services-panel__list li.wide { margin-left: -10px; }
  .back-web {
    position: absolute; left: 0; right: 0; top: 274px;
    text-align: center; font-size: 19px; letter-spacing: 1.6px; color: var(--ink);
  }
</style>
</head>
<body>
<main class="sheet">
  <section class="card card--front" aria-label="Card front">
    <div class="front-accent" aria-hidden="true"></div>
    <h1 class="brand-name">
      <span class="brand-name__main">Brightway Haul</span>
      <span class="brand-name__sub">&amp; Upkeep Services</span>
    </h1>

    <p class="contact-phone">
      <svg viewBox="0 0 16 16" aria-hidden="true">
        <circle cx="8" cy="8" r="7.3" fill="none" stroke="var(--brand-blue)" stroke-width="1.2"/>
        <path d="M5.4 4.2c.4-.3.8-.2 1 .2l.7 1.3c.2.4.1.7-.2 1l-.5.4c.3.8 1 1.6 1.9 2.1l.4-.5c.3-.3.6-.4 1-.2l1.2.7c.4.2.5.7.2 1l-.6.7c-.5.5-1.3.5-2 .1-1.8-1-3.2-2.5-4-4.3-.3-.7-.2-1.4.3-1.9z" fill="var(--brand-blue)"/>
      </svg>
      0487650392
    </p>
    <p class="contact-web">www.brightwayhaul.com.au</p>
    <p class="contact-email">
      <svg viewBox="0 0 11 9" aria-hidden="true">
        <rect x="0" y="0" width="11" height="9" rx="1" fill="var(--brand-blue)"/>
        <path d="M.8 1.2 5.5 5 10.2 1.2" fill="none" stroke="#fff" stroke-width="1"/>
      </svg>
      brightwayhaulandupkeep@mailbox.example
    </p>
  </section>

  <section class="card card--back" aria-label="Card back">
    <div class="back-accent" aria-hidden="true"></div>
    <div class="services-panel">
      <h2 class="services-panel__title">Services we offer</h2>
      <ul class="services-panel__list">
        <li>• CLEAN • MOVE</li>
        <li class="wide">• GENERAL MAINTENANCE AND REPAIRS.</li>
      </ul>
    </div>
    <p class="back-web">www.brightwayhaul.com.au</p>
  </section>
</main>
</body>
</html>
```